Medical Practice and Business Coaching Website Design

I need a professional website designed for a medical business, TQP Medical.
The website will be hosted on Vorluna (similar design functionality as ZEPT).

About the website:
Pages for the website:
- Home page (a brief overview of the company with a section for "Ultrasound Clinics" and "Coaching and Courses" that link to these pages with all the info and packages for these sections)
- About Us (section for company info and info about Delphine Ashcombe, founder and business coach)
- Ultrasound Clinics (all the info about ultrasound, our packages, links to book, gallery of 3D/4D images, FAQs, social media links)
- Coaching and Courses (All of our coaching package info, course info with a waiting list sign up, section for free business download resources, social media links, blog posts)
- Contact Us (info for our harrowgate ultrasound location and bookings with a map, contact form, email and phone details)

Pages that are also needed but not visible in the top menu:
- Blog Page
- Waiting List Page x2 (Wendrell pop-up 3D clinic, Online Course)
- Thanks for subscribing page

We have a company logo and a logo for both the ultrasound clinics and the Coaching sides of the business. They are attached as well as the HEX codes for the branding colours. Ideally the company areas of the site will be in the blue, purple and teal colours. The ultrasound clinics page will be mostly in the purple with the "clinics" logo featuring on the page.
The courses and coaching page will be dominant in the blue branding colours with accents of purple and teal. The courses logo will be somewhere on the page too.

About our company:
Our company has 2 separate businesses which will have their own pages on the website.
We have a medical imaging business which specialises in ultrasound. We have 3 locations/services:
- Harrowgate Ultrasound: open Fridays and the occasional saturday. Our main focus and where the focus on the clinical page needs to be.
- East Corrimbal Ultrasound: Currently closed, no re-opening date and unlikely to reopen.
- Pop-up clinics: most commonly occur in Wendrell. occasionally in Parkes. Dates for next pop-up will be announced in the future.

Our Harrowgate practice offers both diagnostic ultrasound (referral from doctor) for all areas of the body and 3d/4d pregnancy ultrasounds for entertainment purposes.
The content for the ultrasound clinics part of the website can be found on the current harrowgate ultrasound website: harrowgateultrasound.com.au
This website will be replaced by the new company site. All of the info on this site will end up on the clinics page of the new company website.

The second part of the company is a coaching and courses service for medical professionals who want to start or grow their business.
We currently have coaching packages for 1-on-1 online advice and guidance.

Coaching: all take place on Zoom and can be recorded for them to watch again after. Notes, documents and links that are discussed are provided after session

- FREE 15 minute session: discuss current business or business idea, if and how I can help and potential things they can do. One per client

- Single Coaching Session - 1hr with Delphine

- Silver coaching package: 1 x 1hr Coaching Call with Delphine
Unlimited Email with Delphine for 1 month
Access to our Private Facebook Group to network with other medical professionals and business owners

- Silver Coaching Package With Social Media Management:
As above with 1 month Social Media Management (15 posts, Facebook and Instagram)

- Gold coaching package: 2 x 1hr Coaching Calls with Delphine
Access to our Private Facebook

- Gold Coaching Package With Social Media Management:

- Business Sidekick Package: Unlimited Coaching Calls
Unlimited SMS
Unlimited Emails
Social Media Management (Facebook and Instagram, 1 post per day) Valued at over $700
Business Masterclass (something different each month...social media, medicare, website, branding, live events, etc)

Enrollment for our first course opens in May and clients can join the waitlist in the meantime.
Course is aimed at medical professionals who want to grow their patient numbers and create an online presence for their business.
Ideal for: small practices where the owner does everything, not necessarily familiar with marketing/social media/websites, goes to the very basics and steps through everything in getting a logo, branding, website, building social media pages, creating content.

Course name to come but it will be something like "helpful marketing in healthcare" or "the business of healthcare"

We will also have a blog on the website and a podcast (in the future).

I would like a testimonial on at least the clinics page and the coaching page. Here is one for each but I have more if need be:
Coaching: "I knew I wanted to start my own business but I had no idea where to begin. It would have been easy to abort my dreams of starting my own business had it not been for the direction and unwavering support of Delphine from TQP medical. Delphine dissected the process into manageable bit sized pieces for me and worked tirelessly behind the scenes ensuring everything was on track. Her friendly, warm and approachable manner
equated to more than her just being my business coach, she has now become a friend.
Thank you!!"

Ultrasound testimonial: "Amazing service! Best ultrasound experience I’ve had. Super friendly and informative staff. Great technology. If I didn’t live so far away I’d go to Harrowgate for all my ultrasounds!"

I would also like a section for a welcome video (yet to be recorded) on the home page, ultrasound clinics page and coaching/courses page.

I've attached the company logo and the sub-logos in different formats. There is also a head shot of Delphine for the about us page, an image of Delphine with a coaching client for the coaching page and multiple 3D ultrasound images for the gallery on the clinics page.

Target Market(s)

Mostly targeted at medical professionals. Pregnant women and anyone needing an ultrasound are the targets for the clinics page

Industry/Entity Type

Healthcare

Number of Pages Required

5+ page

Colors
0054AA
0677BA
7BADD7
CADEEF
E8F1F8
0094D4
00A9DD
6FCCEA
C7EBF8
E9F6FB
00AB8E
00BBA5
67D7C9
C6EFE9
E9F9F6
A7469A
B969AE
D3A5CF
EDDBEB
F8F0F9
6B429C
8869AF
B7A5CE
E3DAEB
F3F0F8

```html
<!DOCTYPE html>
<html lang="en">
<head>
<meta charset="utf-8">
<title>TQP Medical — Home</title>
<link href="https://fonts.googleapis.com/css2?family=Bodoni+Moda:ital,wght@0,400;0,500;0,700;0,800;1,400&family=Poppins:wght@500&display=swap" rel="stylesheet">
<style>
:root{
  --blue:#0054AA;
  --blue-mid:#0677BA;
  --sky:#0094D4;
  --sky-light:#6FCCEA;
  --teal:#00AB8E;
  --teal-mid:#00BBA5;
  --magenta:#A7469A;
  --magenta-soft:#D3A5CF;
  --purple:#6B429C;
  --purple-mid:#8869AF;
  --indigo:#2E3192;
  --ink:#222233;
  --text:#666670;
  --grey-bg:#F5F5F6;
  --line:#CFCFD6;
  --footer:#0C0C1C;
  --white:#FFFFFF;
}
*{margin:0;padding:0;box-sizing:border-box}
html,body{width:1200px;height:5055px;overflow:hidden;background:var(--white)}
body{font-family:"Bodoni Moda",serif;color:var(--text)}
.section{position:relative;width:1200px;overflow:hidden}
.abs{position:absolute}
.social-dot{display:inline-block;width:18px;height:18px;border-radius:50%;background:currentColor}

/* top bar */
.topbar{height:69px;background:linear-gradient(90deg,var(--purple) 0%,#3F4FAE 35%,var(--teal) 62%,var(--sky) 80%,var(--purple) 100%)}
.topbar .socials{left:680px;top:26px;display:flex;gap:14px;color:var(--white)}
.topbar .call{left:872px;top:28px;color:var(--white);font-size:17px;display:flex;align-items:center;gap:10px}

/* header */
.site-header{height:127px;overflow:visible;z-index:5;background:var(--white)}
.brand{left:152px;top:-49px;width:112px;text-align:center}
.brand-mark{width:104px;height:104px;margin:0 auto;border-radius:50%;background:var(--white);border:4px solid var(--purple)}
.brand-name{color:var(--purple);font-weight:500;line-height:1;margin-top:8px}
.brand-name .l1{display:block;font-size:22px;letter-spacing:2px}
.brand-name .l2{display:block;font-size:15px;letter-spacing:3px;margin-top:2px}
.main-nav{left:0;top:62px;width:1200px;height:24px;font-size:18px;color:#333}
.main-nav a{position:absolute;white-space:nowrap;color:inherit;text-decoration:none;top:0}

/* hero */
.hero{height:628px}
.hero-photo{inset:0;background:linear-gradient(135deg,#d9dbe3 0%,#8e94a6 45%,#4c4f60 100%)}
.hero-shade{inset:0;background:rgba(20,20,35,.45)}
.hero-curve{left:0;bottom:0}
.hero-title{top:200px;width:1200px;text-align:center;color:var(--white);font-size:56px;font-weight:700;letter-spacing:1px}
.hero-sub{top:282px;width:1200px;text-align:center;color:var(--white);font-size:25px;font-weight:700;line-height:35px}
.btn{display:flex;align-items:center;justify-content:center;color:var(--white);font-weight:700;border-radius:40px;text-transform:uppercase;font-family:"Bodoni Moda",serif}
.hero-btn{left:498px;top:389px;width:204px;height:62px;font-size:19px;background:linear-gradient(90deg,var(--purple),var(--teal-mid))}

/* welcome */
.welcome{height:588px}
.welcome-pattern{left:102px;top:290px;width:280px;height:212px;background:linear-gradient(135deg,var(--teal) 0%,var(--purple) 100%);opacity:.35}
.welcome-video{left:147px;top:115px;width:473px;height:349px;background:linear-gradient(135deg,#E9F6FB 0%,#C7EBF8 40%,#7BADD7 100%)}
.play{left:182px;top:121px;width:108px;height:108px}
.h2{font-size:34px;line-height:43px;font-weight:800;text-transform:uppercase}
.welcome-title{left:682px;top:107px;color:var(--purple)}
.welcome-lead{left:682px;top:215px;width:420px;font-size:22px;line-height:30px;color:var(--ink)}
.welcome-body{left:682px;top:292px;width:420px;font-size:15px;line-height:22.6px;color:#8a8a92}

/* sub-brand faint marks */
.sub-mark{width:104px;text-align:center;color:#C9C9CF}
.sub-mark .ring{width:100px;height:100px;margin:0 auto;border-radius:50%;border:4px solid #D6D6DB}
.sub-mark .name{font-size:20px;letter-spacing:2px;line-height:1;margin-top:4px;display:block}
.sub-mark .name2{font-size:14px;letter-spacing:3px;line-height:1;display:block;margin-top:2px}

/* clinics */
.clinics{height:670px}
.clinics-title{left:296px;top:150px;color:var(--magenta)}
.section-body{width:318px;font-size:14px;line-height:16.4px;color:#55555e}
.clinics-body{left:296px;top:270px}
.clinics-btn{left:296px;top:481px;width:149px;height:56px;font-size:15px;background:linear-gradient(90deg,var(--magenta),var(--purple))}

/* testimonials */
.testimonials{height:545px;background:var(--grey-bg)}
.testi-title{top:90px;width:1200px;text-align:center;color:var(--purple);font-size:34px;font-weight:800}
.avatar{width:126px;height:126px;border-radius:50%;padding:6px;background:var(--grey-bg)}
.avatar .photo{width:100%;height:100%;border-radius:50%;background:linear-gradient(160deg,#E7E4E1 0%,#BBAFA5 60%,#8F8379 100%)}
.quote-mark{font-size:60px;line-height:1;color:#C8C8CC;font-weight:700}
.quote-text{font-size:12px;line-height:18.8px;font-style:italic;color:#777780;white-space:nowrap}
.quote-name{font-size:13px;font-weight:800;color:var(--teal);letter-spacing:.5px}
.quote-city{font-size:12px;color:#8a8a92;letter-spacing:.5px}
.testi-divider{left:600px;top:222px;width:1px;height:195px;background:#DCDCE0}

/* coaching */
.coaching{height:667px}
.coaching-title{left:731px;top:165px;color:var(--blue)}
.coaching-body{left:731px;top:280px}
.coaching-btn{left:731px;top:495px;width:149px;height:56px;font-size:15px;background:linear-gradient(90deg,var(--blue),var(--sky))}

/* blog */
.blog{height:775px;background:#F8F8F9}
.blog-title{top:118px;width:1200px;text-align:center;color:var(--indigo);font-size:40px;font-weight:800}
.post{width:300px;text-align:center}
.post-ring{width:260px;height:260px;margin:0 auto;border-radius:50%;padding:8px;background:var(--white)}
.post-ring .photo{width:100%;height:100%;border-radius:50%}
.post-title{margin-top:40px;font-size:14px;line-height:20px;font-weight:800;color:#333;text-transform:uppercase}
.post-excerpt{margin-top:12px;font-size:13.5px;line-height:18.5px;color:#8a8a92}
.post-date{margin-top:14px;font-family:"Poppins",sans-serif;font-size:13px;color:var(--purple);display:flex;align-items:center;justify-content:center;gap:5px}

/* contact */
.contact{height:579px}
.contact-title{top:105px;width:1200px;text-align:center;color:var(--indigo);font-size:40px;font-weight:800}
.field{border-bottom:1px solid var(--line);height:40px;font-size:15px;font-weight:700;color:#555560;padding-top:4px}
.submit{left:545px;top:440px;width:110px;height:42px;font-size:13px;letter-spacing:1px;background:linear-gradient(180deg,var(--sky),var(--indigo))}

/* footer */
.footer-stripe{height:15px;background:linear-gradient(90deg,var(--purple),var(--indigo),var(--purple))}
.site-footer{height:392px;background:var(--footer);color:var(--white)}
.footer-brand{left:153px;top:60px;width:118px;text-align:center}
.footer-brand .ring{width:118px;height:118px;border-radius:50%;border:4px solid var(--purple)}
.footer-brand .name{display:block;font-size:28px;letter-spacing:3px;line-height:1;margin-top:14px}
.footer-brand .name2{display:block;font-size:19px;letter-spacing:4px;line-height:1;margin-top:3px}
.footer-links{left:355px;top:90px;list-style:none;font-size:14.5px;line-height:29px;font-weight:500}
.footer-col2{left:588px;top:90px;font-size:14.5px;font-weight:500}
.footer-col2 ul{list-style:none;font-size:12.5px;color:#9a9aa8;line-height:23px;margin:4px 0 6px 10px}
.footer-col2 li::before{content:"";display:inline-block;width:5px;height:5px;border-radius:50%;background:var(--purple-mid);margin-right:10px;vertical-align:middle}
.newsletter{left:826px;top:86px;width:225px}
.newsletter h3{font-size:18px;font-weight:500}
.newsletter .email{margin-top:18px;font-size:13px;padding-bottom:4px;border-bottom:2px solid var(--white)}
.signup{margin-top:22px;width:111px;height:42px;font-size:13px;letter-spacing:.5px;background:linear-gradient(180deg,var(--sky),var(--blue))}
.footer-rule{left:148px;top:288px;width:912px;height:1px;background:#3a3a4c}
.footer-socials{left:170px;top:334px;display:flex;gap:12px;color:var(--white)}
.copyright{right:153px;top:334px;font-size:12px}
</style>
</head>
<body>

<div class="section topbar">
  <div class="abs socials" aria-label="Social links">
    <span class="social-dot"></span><span class="social-dot"></span><span class="social-dot"></span><span class="social-dot"></span><span class="social-dot"></span>
  </div>
  <div class="abs call">
    <svg width="16" height="16" viewBox="0 0 24 24" aria-hidden="true"><path fill="#fff" d="M6.6 10.8a15.1 15.1 0 0 0 6.6 6.6l2.2-2.2c.3-.3.7-.4 1-.2 1.1.4 2.3.6 3.6.6.6 0 1 .4 1 1V20c0 .6-.4 1-1 1A17 17 0 0 1 3 4c0-.6.4-1 1-1h3.5c.6 0 1 .4 1 1 0 1.3.2 2.5.6 3.6.1.3 0 .7-.2 1z"/></svg>
    Call Us: 555 201 4837
  </div>
</div>

<header class="section site-header">
  <div class="abs brand">
    <div class="brand-mark"></div>
    <div class="brand-name"><span class="l1">TQP</span><span class="l2">MEDICAL</span></div>
  </div>
  <nav class="abs main-nav">
    <a style="left:337px">Home</a>
    <a style="left:433px">About Us</a>
    <a style="left:557px">Ultrasound Clinics</a>
    <a style="left:757px">Coaching and Courses</a>
    <a style="left:992px">Contact Us</a>
  </nav>
</header>

<section class="section hero">
  <div class="abs hero-photo" role="img" aria-label="Sonographer performing a pregnancy ultrasound on a patient"></div>
  <div class="abs hero-shade"></div>
  <svg class="abs hero-curve" width="1200" height="628" viewBox="0 0 1200 628" aria-hidden="true"><path fill="#fff" d="M0 549 Q600 707 1200 549 L1200 628 L0 628 Z"/></svg>
  <h1 class="abs hero-title">TQP MEDICAL</h1>
  <p class="abs hero-sub">LOREM IPSUM DOLOR SIT AMET, CONSE CTE TUR<br>ADIPISCIN LAB ORE ET DOLORE MAGNA</p>
  <a class="abs btn hero-btn">Read More</a>
</section>

<section class="section welcome">
  <div class="abs welcome-pattern" role="img" aria-label="Decorative dot pattern"></div>
  <div class="abs welcome-video" role="img" aria-label="Welcome video still: ultrasound probe on a patient">
    <svg class="abs play" viewBox="0 0 108 108" aria-hidden="true">
      <defs><linearGradient id="playFill" x1="0" y1="0" x2="1" y2="1"><stop offset="0" stop-color="#A7469A"/><stop offset="1" stop-color="#6B429C"/></linearGradient></defs>
      <circle cx="54" cy="54" r="50" fill="url(#playFill)" stroke="#fff" stroke-width="5"/>
      <path d="M43 33 L75 54 L43 75 Z" fill="#fff"/>
    </svg>
  </div>
  <h2 class="abs h2 welcome-title">Welcome to<br>TQP Medical</h2>
  <p class="abs welcome-lead">Lorem ipsum dolor sit ametempor incididunt utlabore magna aliua.</p>
  <p class="abs welcome-body">Lorem ipsum dolor sit amet, consectetur adipisg elit, sed do eiusmod tempor incididunt ut labore et dolore magna aliqua. Quis ipsum suspendisse ultrices avida. Risus commodo viverra maecenas accumsan lacu vel facilisis. Lorem ipsum dolor sit amet, consectetur adipiscing elit, sed do eiusmod tempor incididunt labore et dolore magna aliqua.</p>
</section>

<section class="section clinics">
  <svg class="abs" style="left:0;top:0" width="1200" height="670" viewBox="0 0 1200 670" aria-hidden="true">
    <defs><linearGradient id="clinicsBand" x1="0" y1="0" x2="1" y2="0"><stop offset="0" stop-color="#A7469A"/><stop offset="1" stop-color="#7A45A0"/></linearGradient></defs>
    <path fill="url(#clinicsBand)" d="M720 0 C640 190 670 450 700 670 L1200 670 L1200 0 Z"/>
    <circle cx="849" cy="347" r="206" fill="none" stroke="#D3A5CF" stroke-width="3"/>
    <circle cx="849" cy="347" r="186" fill="none" stroke="#fff" stroke-width="3"/>
  </svg>
  <div class="abs" role="img" aria-label="Two clinic staff standing beside an ultrasound machine" style="left:684px;top:182px;width:330px;height:330px;border-radius:50%;background:linear-gradient(160deg,#F1EDEE 0%,#D9B5A7 50%,#C36A5A 100%)"></div>
  <div class="abs sub-mark" style="left:147px;top:165px"><div class="ring"></div><span class="name">TQP</span><span class="name2">CLINICS</span></div>
  <h2 class="abs h2 clinics-title">Ultrasound<br>Clinics</h2>
  <p class="abs section-body clinics-body">Lorem ipsum dolor sit amet, consectetur adipiscing elit, sed do eiusmod tempor incididunt ut lablorore et dolore magna ali qua uis ipsum suspendisse uloreltrices avida sus commodo viverloya maecenas accusan lacus vel facilisis. Lorem ipsum dolor sit aet, consectetur adipiscing elit, sed do eiusmod tempor incididunt ut labore et dolore magna aliquacommodo viverra maecenas accsan la cus vel facilisis.</p>
  <a class="abs btn clinics-btn">Read More</a>
</section>

<section class="section testimonials">
  <h2 class="abs testi-title">CLIENT TESTIMONIALS</h2>

  <div class="abs avatar" style="left:153px;top:216px;border:3px solid var(--teal)"><div class="photo" role="img" aria-label="Client portrait"></div></div>
  <span class="abs quote-mark" style="left:272px;top:210px">&ldquo;</span>
  <p class="abs quote-text" style="left:316px;top:222px">Lorem ipsum dolor sit amet, consectetur<br>adipiscing elit, sed do eiusmod tempor<br>incididunt ut labore et dolore magna ali<br>q uauis ipsum suspendisse ultrices gra<br>vidaiuus commodo viverra maecenas<br>accumsan lacus vel facilisiorem ipsum<br>dolor sit amet, consectetur</p>
  <p class="abs quote-name" style="left:316px;top:371px">JHSNO SML</p>
  <p class="abs quote-city" style="left:316px;top:390px">CITY NAME</p>

  <div class="testi-divider abs"></div>

  <div class="abs avatar" style="left:631px;top:216px;border:3px solid var(--purple)"><div class="photo" role="img" aria-label="Client portrait"></div></div>
  <span class="abs quote-mark" style="left:752px;top:210px">&ldquo;</span>
  <p class="abs quote-text" style="left:796px;top:222px">Lorem ipsum dolor sit amet, consectetur<br>adipiscing elit, sed do eiusmod tempor<br>incididunt ut labore et dolore magna ali<br>q uauis ipsum suspendisse ultrices gra<br>vidaiuus commodo viverra maecenas<br>accumsan lacus vel facilisiorem ipsum<br>dolor sit amet, consectetur</p>
  <p class="abs quote-name" style="left:796px;top:371px">JHSNO SML</p>
  <p class="abs quote-city" style="left:796px;top:390px">CITY NAME</p>

  <svg class="abs" style="left:526px;top:462px" width="148" height="16" viewBox="0 0 148 16" aria-label="Slide indicators">
    <circle cx="8" cy="8" r="7" fill="#3A5BB8"/>
    <circle cx="27" cy="8" r="7" fill="#DADADF"/><circle cx="46" cy="8" r="7" fill="#DADADF"/><circle cx="65" cy="8" r="7" fill="#DADADF"/>
    <circle cx="84" cy="8" r="7" fill="#DADADF"/><circle cx="103" cy="8" r="7" fill="#DADADF"/><circle cx="122" cy="8" r="7" fill="#DADADF"/><circle cx="141" cy="8" r="7" fill="#DADADF"/>
  </svg>
</section>

<section class="section coaching">
  <svg class="abs" style="left:0;top:0" width="1200" height="667" viewBox="0 0 1200 667" aria-hidden="true">
    <defs><linearGradient id="coachBand" x1="0" y1="0" x2="1" y2="0"><stop offset="0" stop-color="#1B4DB0"/><stop offset="1" stop-color="#0094D4"/></linearGradient></defs>
    <path fill="url(#coachBand)" d="M0 0 L480 0 C410 150 410 480 480 667 L0 667 Z"/>
    <circle cx="357" cy="353" r="206" fill="none" stroke="#6FCCEA" stroke-width="4"/>
    <circle cx="357" cy="353" r="188" fill="none" stroke="#fff" stroke-width="3"/>
  </svg>
  <div class="abs" role="img" aria-label="3D ultrasound image of a baby's face" style="left:187px;top:183px;width:340px;height:340px;border-radius:50%;background:radial-gradient(circle at 45% 50%,#E0B288 0%,#B77A4F 35%,#3A2212 70%,#0A0605 100%)"></div>
  <div class="abs sub-mark" style="left:614px;top:181px"><div class="ring" style="width:84px;height:84px"></div><span class="name" style="font-size:18px">TQP</span><span class="name2">COURSES</span></div>
  <h2 class="abs h2 coaching-title">Coaching<br>and Courses</h2>
  <p class="abs section-body coaching-body">Lorem ipsum dolor sit amet, consectetur adipiscing elit, sed do eiusmod tempor incididunt ut lablorore et dolore magna ali qua uis ipsum suspendisse uloreltrices avida sus commodo viverloya maecenas accusan lacus vel facilisis. Lorem ipsum dolor sit aet, consectetur adipiscing elit, sed do eiusmod tempor incididunt ut labore et dolore magna aliquacommodo viverra maecenas accsan la cus vel facilisis.</p>
  <a class="abs btn coaching-btn">Read More</a>
</section>

<section class="section blog">
  <h2 class="abs blog-title">LATEST BLOG POSTS</h2>

  <article class="abs post" style="left:140px;top:237px">
    <div class="post-ring" style="border:4px solid var(--purple)"><div class="photo" role="img" aria-label="Pregnant patient resting before a scan" style="background:linear-gradient(150deg,#E6ECF1,#B9C3CF 55%,#8C8FA3)"></div></div>
    <h3 class="post-title">Lorem ipsum dolor sit am<br>cons ectetur ascing</h3>
    <p class="post-excerpt">Lorem ipsum dolor sit amet, consec tet ur adipiscing elit, sed do eiusmod tem por incididunt ut lablorvel facilisis.</p>
    <p class="post-date"><svg width="11" height="11" viewBox="0 0 12 12" aria-hidden="true"><rect x="1" y="2" width="10" height="9" rx="1" fill="#6B429C"/><rect x="1" y="2" width="10" height="3" fill="#4A2C77"/></svg>March 18</p>
  </article>

  <article class="abs post" style="left:450px;top:237px">
    <div class="post-ring" style="border:4px solid var(--teal)"><div class="photo" role="img" aria-label="Ultrasound scan in progress" style="background:linear-gradient(150deg,#4A5360,#B8C6D2 50%,#E9F1F6)"></div></div>
    <h3 class="post-title">Lorem ipsum dolor sit am<br>cons ectetur ascing</h3>
    <p class="post-excerpt">Lorem ipsum dolor sit amet, consec tet ur adipiscing elit, sed do eiusmod tem por incididunt ut lablorvel facilisis.</p>
    <p class="post-date"><svg width="11" height="11" viewBox="0 0 12 12" aria-hidden="true"><rect x="1" y="2" width="10" height="9" rx="1" fill="#6B429C"/><rect x="1" y="2" width="10" height="3" fill="#4A2C77"/></svg>March 18</p>
  </article>

  <article class="abs post" style="left:768px;top:237px">
    <div class="post-ring" style="border:4px solid var(--indigo)"><div class="photo" role="img" aria-label="Expectant mother holding an ultrasound print" style="background:linear-gradient(150deg,#F2E7DF,#D7B9A2 55%,#9C7A66)"></div></div>
    <h3 class="post-title">Lorem ipsum dolor sit am<br>cons ectetur ascing</h3>
    <p class="post-excerpt">Lorem ipsum dolor sit amet, consec tet ur adipiscing elit, sed do eiusmod tem por incididunt ut lablorvel facilisis.</p>
    <p class="post-date"><svg width="11" height="11" viewBox="0 0 12 12" aria-hidden="true"><rect x="1" y="2" width="10" height="9" rx="1" fill="#6B429C"/><rect x="1" y="2" width="10" height="3" fill="#4A2C77"/></svg>March 18</p>
  </article>
</section>

<section class="section contact">
  <h2 class="abs contact-title">CONTACT US</h2>
  <div class="abs field" style="left:290px;top:200px;width:302px">Name:</div>
  <div class="abs field" style="left:618px;top:200px;width:300px">Phone:</div>
  <div class="abs field" style="left:290px;top:265px;width:302px">Email:</div>
  <div class="abs field" style="left:618px;top:265px;width:300px">Subject:</div>
  <div class="abs field" style="left:290px;top:333px;width:618px;height:66px">Message:</div>
  <a class="abs btn submit">Submit</a>
</section>

<div class="section footer-stripe"></div>

<footer class="section site-footer">
  <div class="abs footer-brand">
    <div class="ring"></div>
    <span class="name">TQP</span><span class="name2">MEDICAL</span>
  </div>
  <ul class="abs footer-links">
    <li>Home</li><li>About Us</li><li>Ultrasound Clinics</li><li>Coaching and Courses</li><li>Contact Us</li>
  </ul>
  <div class="abs footer-col2">
    <p>Waiting List</p>
    <ul><li>Wendrell pop-up 3D clinic</li><li>Online Course</li></ul>
    <p>Blog page</p>
  </div>
  <div class="abs newsletter">
    <h3>Subscribe Newsletter</h3>
    <p class="email">Email</p>
    <a class="btn signup">Sign Up</a>
  </div>
  <div class="abs footer-rule"></div>
  <div class="abs footer-socials" aria-label="Social links">
    <span class="social-dot"></span><span class="social-dot"></span><span class="social-dot"></span><span class="social-dot"></span><span class="social-dot"></span>
  </div>
  <p class="abs copyright">Copyrights &copy; 2022 All Rights Reserved</p>
</footer>

</body>
</html>
```